BRIGHT CORAL INC , CELL PHONE STORE

We need website design . we already have one but not happy with it www.brightcoralinc.example
we cell phones provide service ,phone repair ,
phone accessories.
online sale payment via PayVerra
shipping by QDMX

Industry/Entity Type

Cell Phone

Number of Pages Required

5+ page

Font styles to use
Serif
Sans Serif

Colors
3176b5

Requirements
Must have
• online sale via PayVerra
Nice to have
• email address

```html
<!DOCTYPE html>
<html lang="en">
<head>
<meta charset="utf-8">
<title>Bright Coral Inc — Cell Phone Store</title>
<link href="https://fonts.googleapis.com/css2?family=Nunito+Sans:wght@400;600;700;800&display=swap" rel="stylesheet">
<style>
:root{
  --brand:#3176b5;
  --brand-dark:#2a67a0;
  --accent:#e0383e;
  --ink:#1e1e1e;
  --muted:#6d6d6d;
  --line:#dcdcdc;
  --soft:#f4f4f4;
  --white:#ffffff;
}
*{box-sizing:border-box;margin:0;padding:0}
html,body{width:1200px;height:2773px;overflow:hidden;background:var(--white)}
body{font-family:"Nunito Sans",Arial,sans-serif;color:var(--ink);position:relative}
.wrap{position:absolute;left:98px;width:1004px}
svg{display:block}

/* top bar */
.topbar{position:absolute;top:0;left:0;width:1200px;height:30px;background:var(--brand);color:var(--white);font-size:12px}
.topbar .wrap{top:0;height:30px;display:flex;align-items:center;justify-content:space-between}
.topbar .group{display:flex;align-items:center;gap:10px}
.topbar .item{display:flex;align-items:center;gap:6px}
.topbar .sep{opacity:.7}

/* header */
.header{position:absolute;top:30px;left:0;width:1200px;height:85px;border-bottom:1px solid var(--line)}
.logo{position:absolute;left:98px;top:34px;font-size:24px;font-weight:700;color:var(--accent);letter-spacing:.5px;display:flex;align-items:center;gap:8px}
.logo .dot{width:10px;height:10px;background:var(--accent)}
.search{position:absolute;left:453px;top:18px;width:444px;height:42px;border:1px solid #cfcfcf;display:flex}
.search span{flex:1;font-size:12px;color:#8a8a8a;padding:13px 16px}
.search .btn{width:50px;border-left:1px solid #cfcfcf;display:flex;align-items:center;justify-content:center}
.cart{position:absolute;left:943px;top:16px;display:flex;gap:14px}
.cart .label{font-size:14px;line-height:20px}
.cart .sub{font-size:11px;color:var(--muted)}

/* nav */
.nav{position:absolute;top:115px;left:0;width:1200px;height:42px}
.categories{position:absolute;left:98px;top:0;width:235px;height:42px;background:#eef1f4;border:1px solid #cfd6dd;color:var(--brand);font-size:17px;font-weight:700;display:flex;align-items:center;justify-content:center;gap:10px}
.menu{position:absolute;right:98px;top:0;height:42px;display:flex;gap:50px;align-items:center;font-size:15px;font-weight:700}
.menu .active{color:var(--brand)}

/* hero */
.hero{position:absolute;top:157px;left:0;width:1200px;height:435px;background:linear-gradient(120deg,#9ea4a8 0%,#d9dcde 35%,#c7cacc 60%,#eceded 100%)}
.hero .photo{position:absolute;inset:0}
.hero h1{position:absolute;top:120px;width:1200px;text-align:center;font-size:70px;font-weight:600;letter-spacing:4px;color:var(--white)}
.hero p{position:absolute;top:205px;width:1200px;text-align:center;font-size:20px;color:var(--white)}
.locate{position:absolute;left:364px;top:253px;width:472px;height:45px;display:flex}
.locate .field{flex:1;background:var(--white);display:flex;align-items:center;padding:0 14px;gap:10px;font-size:13px;color:#777}
.locate .field .grow{flex:1}
.locate .go{width:56px;background:var(--brand);color:var(--white);font-weight:700;font-size:15px;display:flex;align-items:center;justify-content:center}
.dots{position:absolute;top:375px;left:532px;display:flex;gap:6px}
.dots i{display:block;width:28px;height:4px;background:var(--white)}
.dots i.on{background:var(--brand)}

/* section heading */
.section-title{position:absolute;width:1200px;left:0;text-align:center;font-size:29px;font-weight:700;letter-spacing:.5px}

/* why repair */
.features{position:absolute;top:734px;left:98px;width:1004px;display:grid;grid-template-columns:repeat(4,1fr);gap:0 0}
.feature{text-align:center}
.feature .ring{width:142px;height:142px;border:1.5px solid #bdbdbd;border-radius:50%;margin:0 auto;display:flex;align-items:center;justify-content:center}
.feature h3{margin-top:26px;font-size:19px;font-weight:600}
.feature p{margin-top:12px;font-size:12px;color:var(--muted);line-height:20px}
.rule{position:absolute;top:1024px;left:98px;width:1004px;height:1px;background:#cfcfcf}

/* tabs */
.tabs{position:absolute;top:1141px;left:312px;display:flex}
.tab{width:192px;height:46px;border:1px solid #cfcfcf;display:flex;align-items:center;justify-content:center;font-size:16px;font-weight:600}
.tab+.tab{border-left:none}
.tab.active{background:var(--brand);border-color:var(--brand);color:var(--white)}

/* products */
.products{position:absolute;top:1243px;left:98px;width:1004px;display:grid;grid-template-columns:repeat(4,236px);column-gap:20px;row-gap:39px}
.product .thumb{height:216px;border:1px solid #e2e2e2;padding:8px}
.product .thumb div{width:100%;height:100%;background:radial-gradient(circle at 50% 50%,#6b7f9c 0%,#2b3442 38%,#f2f2f2 39%,#f2f2f2 100%)}
.product h4{margin-top:25px;font-size:13px;font-weight:400;line-height:22px}
.product .price{margin-top:11px;font-size:18px;font-weight:700;color:var(--accent)}
.product .actions{margin-top:12px;display:flex;gap:4px}
.add{width:134px;height:33px;background:var(--brand);color:var(--white);font-size:12px;font-weight:800;display:flex;align-items:center;justify-content:center;gap:8px}
.icon-btn{width:46px;height:33px;border:1px solid #cfcfcf;display:flex;align-items:center;justify-content:center}
.more{position:absolute;top:2058px;left:484px;width:232px;height:39px;border:1px solid #bdbdbd;color:var(--brand);font-size:13px;font-weight:800;display:flex;align-items:center;justify-content:center;letter-spacing:.3px}

/* brands */
.brands{position:absolute;top:2158px;left:0;width:1200px;height:251px;background:var(--brand)}
.brands h2{position:absolute;top:46px;width:1200px;text-align:center;color:var(--white);font-size:29px;font-weight:600}
.brand-row{position:absolute;top:112px;left:98px;display:flex;gap:14px}
.brand{width:189px;height:80px;background:var(--white);display:flex;align-items:center;justify-content:center;font-size:18px;font-weight:700;color:#333}
.arrow{position:absolute;top:136px}

/* footer */
.footer-cols{position:absolute;top:2468px;left:98px;width:1004px;height:180px}
.col{position:absolute;top:0}
.col h5{font-size:19px;font-weight:600;margin-bottom:14px}
.col ul{list-style:none;font-size:12px;color:#444;line-height:27.7px}
.col-sep{position:absolute;top:4px;width:1px;height:190px;background:#e0e0e0}
.col p{font-size:12px;color:#555;margin-bottom:12px}
.subscribe{display:flex;width:323px;height:36px}
.subscribe span{flex:1;border:1px solid #cfcfcf;font-size:12px;color:#666;padding:10px 12px}
.subscribe b{width:92px;background:var(--brand);color:var(--white);font-size:12px;font-weight:800;display:flex;align-items:center;justify-content:center}
.social{display:flex;gap:9px;margin-top:12px}
.social i{width:34px;height:34px;border-radius:50%;background:var(--brand);display:block}
.bottom{position:absolute;top:2700px;left:98px;width:1004px;border-top:1px solid #e0e0e0;height:60px;display:flex;align-items:center;justify-content:space-between;font-size:12px;color:#444}
.pay{display:flex;gap:6px;align-items:center}
.pay span{height:30px;padding:0 6px;border:1px solid #cfcfcf;font-size:11px;font-weight:700;color:#333;display:flex;align-items:center}
</style>
</head>
<body>

<div class="topbar">
  <div class="wrap">
    <div class="group">
      <div class="item"><svg width="12" height="12" viewBox="0 0 24 24"><path fill="#fff" d="M6.6 10.8a15 15 0 0 0 6.6 6.6l2.2-2.2c.3-.3.7-.4 1-.2 1.1.4 2.3.6 3.6.6.6 0 1 .4 1 1V20c0 .6-.4 1-1 1A17 17 0 0 1 3 4c0-.6.4-1 1-1h3.5c.6 0 1 .4 1 1 0 1.3.2 2.5.6 3.6.1.3 0 .7-.2 1z"/></svg>1 555 010 4841</div>
      <span class="sep">|</span>
      <div class="item"><svg width="13" height="10" viewBox="0 0 26 20"><rect width="26" height="20" rx="2" fill="#fff"/><path d="M1 2l12 9 12-9" stroke="#3176b5" stroke-width="2" fill="none"/></svg>hello@brightcoralinc.example</div>
    </div>
    <div class="group">
      <div class="item"><svg width="12" height="11" viewBox="0 0 24 22"><path fill="#fff" d="M12 22 2 12A6 6 0 0 1 12 4a6 6 0 0 1 10 8z"/></svg>Wishlist</div>
      <span class="sep">|</span>
      <div class="item"><svg width="11" height="11" viewBox="0 0 24 24"><circle cx="12" cy="7" r="5" fill="#fff"/><path fill="#fff" d="M2 24a10 10 0 0 1 20 0z"/></svg>Login</div>
      <span class="sep">|</span>
      <div class="item"><svg width="11" height="11" viewBox="0 0 24 24"><path fill="#fff" d="M3 17v4h4L19 9l-4-4zM21 7l-4-4 2-2 4 4z"/></svg>Register</div>
    </div>
  </div>
</div>

<header class="header">
  <div class="logo"><span>BRIGHT CORAL INC</span><span class="dot"></span></div>
  <div class="search"><span>SEARCH</span><div class="btn"><svg width="18" height="18" viewBox="0 0 24 24"><circle cx="10" cy="10" r="7" stroke="#777" stroke-width="2.4" fill="none"/><path d="M15 15l7 7" stroke="#777" stroke-width="2.6"/></svg></div></div>
  <div class="cart">
    <svg width="32" height="30" viewBox="0 0 32 30"><path d="M1 3h5l4 17h16l4-12H8" stroke="#e0383e" stroke-width="2.4" fill="none"/><circle cx="12" cy="26" r="2.5" fill="#e0383e"/><circle cx="24" cy="26" r="2.5" fill="#e0383e"/></svg>
    <div><div class="label">My Cart</div><div class="sub">0 item(s) | $ 0.00 ▾</div></div>
  </div>
</header>

<nav class="nav">
  <div class="categories"><svg width="16" height="13" viewBox="0 0 16 13"><rect width="16" height="2.4" fill="#3176b5"/><rect y="5.3" width="16" height="2.4" fill="#3176b5"/><rect y="10.6" width="16" height="2.4" fill="#3176b5"/></svg>CATEGORIES</div>
  <div class="menu"><span class="active">HOME</span><span>ABOUT US</span><span>PHONE REPAIR</span><span>PRODUCTS</span><span>CONTACT</span></div>
</nav>

<section class="hero">
  <div class="photo" role="img" aria-label="Close-up of hands repairing an opened smartphone with a screwdriver and tools on a workbench"></div>
  <h1>BRIGHT CORAL INC</h1>
  <p>We provide cell phone service, phone repair, phone accessories</p>
  <div class="locate">
    <div class="field"><svg width="10" height="14" viewBox="0 0 10 14"><path fill="#777" d="M5 0a5 5 0 0 1 5 5c0 4-5 9-5 9S0 9 0 5a5 5 0 0 1 5-5z"/><circle cx="5" cy="5" r="2" fill="#fff"/></svg><span class="grow">Choose Your Location</span><svg width="12" height="8" viewBox="0 0 12 8"><path d="M1 1l5 5 5-5" stroke="#777" stroke-width="1.6" fill="none"/></svg></div>
    <div class="go">GO</div>
  </div>
  <div class="dots"><i class="on"></i><i></i><i></i><i></i></div>
</section>

<h2 class="section-title" style="top:644px">WHY REPAIR AT BRIGHT CORAL?</h2>
<div class="features">
  <div class="feature">
    <div class="ring"><svg width="58" height="40" viewBox="0 0 58 40"><rect x="0" y="2" width="34" height="26" rx="2" fill="#3176b5"/><path d="M36 10h12l8 10v8H36z" fill="#3176b5"/><circle cx="12" cy="32" r="6" fill="#3176b5" stroke="#fff" stroke-width="2"/><circle cx="46" cy="32" r="6" fill="#3176b5" stroke="#fff" stroke-width="2"/></svg></div>
    <h3>Fast Delivery</h3><p>At vero eos et accusamus et iusdio<br>dignissimos ducimus vol</p>
  </div>
  <div class="feature">
    <div class="ring"><svg width="50" height="50" viewBox="0 0 50 50"><path d="M40 3a11 11 0 0 0-12 14L4 41a4 4 0 0 0 5 5l24-24A11 11 0 0 0 47 10l-7 7-6-1-1-6 7-7z" fill="#3176b5"/></svg></div>
    <h3>Direct Home Repair</h3><p>At vero eos et accusamus et iusdio<br>dignissimos ducimus vol</p>
  </div>
  <div class="feature">
    <div class="ring"><svg width="62" height="40" viewBox="0 0 62 40"><rect x="1" y="1" width="60" height="38" rx="2" fill="#3176b5"/><rect x="7" y="6" width="48" height="28" fill="none" stroke="#fff" stroke-width="2"/><circle cx="31" cy="20" r="10" fill="#fff"/><text x="31" y="26" font-size="15" font-weight="700" text-anchor="middle" fill="#3176b5" font-family="Nunito Sans,sans-serif">1</text></svg></div>
    <h3>Cash on Delivery</h3><p>At vero eos et accusamus et iusdio<br>dignissimos ducimus vol</p>
  </div>
  <div class="feature">
    <div class="ring"><svg width="48" height="48" viewBox="0 0 48 48"><rect x="2" y="20" width="10" height="26" fill="#3176b5"/><path d="M15 22 25 4c4 0 6 3 5 7l-2 8h14c3 0 5 3 4 6l-4 17c-1 2-2 4-5 4H15z" fill="#3176b5"/></svg></div>
    <h3>3 Month Warranty</h3><p>At vero eos et accusamus et iusdio<br>dignissimos ducimus vol</p>
  </div>
</div>
<div class="rule"></div>

<h2 class="section-title" style="top:1072px">OUR PRODUCTS</h2>
<div class="tabs"><div class="tab active">FEATURED</div><div class="tab">NEW ARRIVALS</div><div class="tab">BEST SELLER</div></div>

<div class="products">
  <article class="product"><div class="thumb"><div role="img" aria-label="Black smartphone with blue screen, front view"></div></div><h4>At vero eos et accusamus et iusto<br>odio dignissimos ducim</h4><div class="price">$15.00</div><div class="actions"><div class="add"><svg width="12" height="11" viewBox="0 0 24 22"><path fill="#fff" d="M0 2h5l4 13h12l3-10H7z"/><circle cx="10" cy="19" r="2.5" fill="#fff"/><circle cx="19" cy="19" r="2.5" fill="#fff"/></svg>ADD TO CART</div><div class="icon-btn"><svg width="14" height="13" viewBox="0 0 24 22"><path fill="#3176b5" d="M12 22 2 12A6 6 0 0 1 12 4a6 6 0 0 1 10 8z"/></svg></div><div class="icon-btn"><svg width="13" height="13" viewBox="0 0 24 24"><circle cx="12" cy="12" r="11" fill="#3176b5"/><rect x="10.5" y="10" width="3" height="9" fill="#fff"/><circle cx="12" cy="6.5" r="1.8" fill="#fff"/></svg></div></div></article>
  <article class="product"><div class="thumb"><div role="img" aria-label="Two smartphones standing, one with colorful app screen"></div></div><h4>At vero eos et accusamus et iusto<br>odio dignissimos ducim</h4><div class="price">$15.00</div><div class="actions"><div class="add"><svg width="12" height="11" viewBox="0 0 24 22"><path fill="#fff" d="M0 2h5l4 13h12l3-10H7z"/><circle cx="10" cy="19" r="2.5" fill="#fff"/><circle cx="19" cy="19" r="2.5" fill="#fff"/></svg>ADD TO CART</div><div class="icon-btn"><svg width="14" height="13" viewBox="0 0 24 22"><path fill="#3176b5" d="M12 22 2 12A6 6 0 0 1 12 4a6 6 0 0 1 10 8z"/></svg></div><div class="icon-btn"><svg width="13" height="13" viewBox="0 0 24 24"><circle cx="12" cy="12" r="11" fill="#3176b5"/><rect x="10.5" y="10" width="3" height="9" fill="#fff"/><circle cx="12" cy="6.5" r="1.8" fill="#fff"/></svg></div></div></article>
  <article class="product"><div class="thumb"><div role="img" aria-label="Smartphone with gradient wallpaper, angled view"></div></div><h4>At vero eos et accusamus et iusto<br>odio dignissimos ducim</h4><div class="price">$15.00</div><div class="actions"><div class="add"><svg width="12" height="11" viewBox="0 0 24 22"><path fill="#fff" d="M0 2h5l4 13h12l3-10H7z"/><circle cx="10" cy="19" r="2.5" fill="#fff"/><circle cx="19" cy="19" r="2.5" fill="#fff"/></svg>ADD TO CART</div><div class="icon-btn"><svg width="14" height="13" viewBox="0 0 24 22"><path fill="#3176b5" d="M12 22 2 12A6 6 0 0 1 12 4a6 6 0 0 1 10 8z"/></svg></div><div class="icon-btn"><svg width="13" height="13" viewBox="0 0 24 24"><circle cx="12" cy="12" r="11" fill="#3176b5"/><rect x="10.5" y="10" width="3" height="9" fill="#fff"/><circle cx="12" cy="6.5" r="1.8" fill="#fff"/></svg></div></div></article>
  <article class="product"><div class="thumb"><div role="img" aria-label="Tablet and smartphone lying with app icons on screens"></div></div><h4>At vero eos et accusamus et iusto<br>odio dignissimos ducim</h4><div class="price">$15.00</div><div class="actions"><div class="add"><svg width="12" height="11" viewBox="0 0 24 22"><path fill="#fff" d="M0 2h5l4 13h12l3-10H7z"/><circle cx="10" cy="19" r="2.5" fill="#fff"/><circle cx="19" cy="19" r="2.5" fill="#fff"/></svg>ADD TO CART</div><div class="icon-btn"><svg width="14" height="13" viewBox="0 0 24 22"><path fill="#3176b5" d="M12 22 2 12A6 6 0 0 1 12 4a6 6 0 0 1 10 8z"/></svg></div><div class="icon-btn"><svg width="13" height="13" viewBox="0 0 24 24"><circle cx="12" cy="12" r="11" fill="#3176b5"/><rect x="10.5" y="10" width="3" height="9" fill="#fff"/><circle cx="12" cy="6.5" r="1.8" fill="#fff"/></svg></div></div></article>
  <article class="product"><div class="thumb"><div role="img" aria-label="Dark smartphone with app grid, tilted"></div></div><h4>At vero eos et accusamus et iusto<br>odio dignissimos ducim</h4><div class="price">$15.00</div><div class="actions"><div class="add"><svg width="12" height="11" viewBox="0 0 24 22"><path fill="#fff" d="M0 2h5l4 13h12l3-10H7z"/><circle cx="10" cy="19" r="2.5" fill="#fff"/><circle cx="19" cy="19" r="2.5" fill="#fff"/></svg>ADD TO CART</div><div class="icon-btn"><svg width="14" height="13" viewBox="0 0 24 22"><path fill="#3176b5" d="M12 22 2 12A6 6 0 0 1 12 4a6 6 0 0 1 10 8z"/></svg></div><div class="icon-btn"><svg width="13" height="13" viewBox="0 0 24 24"><circle cx="12" cy="12" r="11" fill="#3176b5"/><rect x="10.5" y="10" width="3" height="9" fill="#fff"/><circle cx="12" cy="6.5" r="1.8" fill="#fff"/></svg></div></div></article>
  <article class="product"><div class="thumb"><div role="img" aria-label="Silver smartphone showing a clock and city wallpaper"></div></div><h4>At vero eos et accusamus et iusto<br>odio dignissimos ducim</h4><div class="price">$15.00</div><div class="actions"><div class="add"><svg width="12" height="11" viewBox="0 0 24 22"><path fill="#fff" d="M0 2h5l4 13h12l3-10H7z"/><circle cx="10" cy="19" r="2.5" fill="#fff"/><circle cx="19" cy="19" r="2.5" fill="#fff"/></svg>ADD TO CART</div><div class="icon-btn"><svg width="14" height="13" viewBox="0 0 24 22"><path fill="#3176b5" d="M12 22 2 12A6 6 0 0 1 12 4a6 6 0 0 1 10 8z"/></svg></div><div class="icon-btn"><svg width="13" height="13" viewBox="0 0 24 24"><circle cx="12" cy="12" r="11" fill="#3176b5"/><rect x="10.5" y="10" width="3" height="9" fill="#fff"/><circle cx="12" cy="6.5" r="1.8" fill="#fff"/></svg></div></div></article>
  <article class="product"><div class="thumb"><div role="img" aria-label="Smartphone lying flat with bright blue screen"></div></div><h4>At vero eos et accusamus et iusto<br>odio dignissimos ducim</h4><div class="price">$15.00</div><div class="actions"><div class="add"><svg width="12" height="11" viewBox="0 0 24 22"><path fill="#fff" d="M0 2h5l4 13h12l3-10H7z"/><circle cx="10" cy="19" r="2.5" fill="#fff"/><circle cx="19" cy="19" r="2.5" fill="#fff"/></svg>ADD TO CART</div><div class="icon-btn"><svg width="14" height="13" viewBox="0 0 24 22"><path fill="#3176b5" d="M12 22 2 12A6 6 0 0 1 12 4a6 6 0 0 1 10 8z"/></svg></div><div class="icon-btn"><svg width="13" height="13" viewBox="0 0 24 24"><circle cx="12" cy="12" r="11" fill="#3176b5"/><rect x="10.5" y="10" width="3" height="9" fill="#fff"/><circle cx="12" cy="6.5" r="1.8" fill="#fff"/></svg></div></div></article>
  <article class="product"><div class="thumb"><div role="img" aria-label="Black smartphone with blue screen, front view"></div></div><h4>At vero eos et accusamus et iusto<br>odio dignissimos ducim</h4><div class="price">$15.00</div><div class="actions"><div class="add"><svg width="12" height="11" viewBox="0 0 24 22"><path fill="#fff" d="M0 2h5l4 13h12l3-10H7z"/><circle cx="10" cy="19" r="2.5" fill="#fff"/><circle cx="19" cy="19" r="2.5" fill="#fff"/></svg>ADD TO CART</div><div class="icon-btn"><svg width="14" height="13" viewBox="0 0 24 22"><path fill="#3176b5" d="M12 22 2 12A6 6 0 0 1 12 4a6 6 0 0 1 10 8z"/></svg></div><div class="icon-btn"><svg width="13" height="13" viewBox="0 0 24 24"><circle cx="12" cy="12" r="11" fill="#3176b5"/><rect x="10.5" y="10" width="3" height="9" fill="#fff"/><circle cx="12" cy="6.5" r="1.8" fill="#fff"/></svg></div></div></article>
</div>
<div class="more">VIEW MORE PRODUCTS</div>

<section class="brands">
  <h2>TOP BRANDS</h2>
  <svg class="arrow" style="left:40px" width="20" height="30" viewBox="0 0 20 30"><path d="M16 2 4 15l12 13" stroke="#fff" stroke-width="2.5" fill="none" opacity=".7"/></svg>
  <div class="brand-row">
    <div class="brand">Vantel Mobile</div>
    <div class="brand">Orbix</div>
    <div class="brand">Linkwave</div>
    <div class="brand">Sorano</div>
    <div class="brand">Pomelo</div>
  </div>
  <svg class="arrow" style="left:1142px" width="20" height="30" viewBox="0 0 20 30"><path d="M4 2l12 13L4 28" stroke="#fff" stroke-width="2.5" fill="none" opacity=".7"/></svg>
</section>

<footer>
  <div class="footer-cols">
    <div class="col" style="left:0"><h5>Information</h5><ul><li>About Us</li><li>Careers</li><li>Privacy &amp; Security</li><li>Site Map</li><li>Terms of Use</li><li>Blog</li></ul></div>
    <div class="col-sep" style="left:180px"></div>
    <div class="col" style="left:205px"><h5>Help &amp; support</h5><ul><li>Login</li><li>New Customers</li><li>Products</li><li>Phone Repair</li><li>Frequently Asked Questions</li><li>How to Order</li></ul></div>
    <div class="col-sep" style="left:410px"></div>
    <div class="col" style="left:453px"><h5>My Account</h5><ul><li>Delivery Information</li><li>My Account</li><li>Order Tracking</li><li>Reminder Service</li><li>Shipping, Returns &amp; Fees</li></ul></div>
    <div class="col-sep" style="left:640px"></div>
    <div class="col" style="left:679px">
      <h5>Email Subscription</h5>
      <p>Register your email address to get information about us</p>
      <div class="subscribe"><span>Email Address</span><b>SUBSCRIBE</b></div>
      <h5 style="margin-top:16px;margin-bottom:0">Stay Connected</h5>
      <div class="social" aria-label="Social links"><i></i><i></i><i></i><i></i><i></i><i></i><i></i></div>
    </div>
  </div>
  <div class="bottom">
    <span>Copyrights © 2017, Bright Coral Inc. All Rights Reserved &nbsp;|&nbsp; Privacy Policy | Terms of Use | Feedback</span>
    <div class="pay"><span>Shipora</span><span>Cardino</span><span>Norvia</span><span>Amplo</span><span>Dovex</span></div>
  </div>
</footer>

</body>
</html>
```